Progressive Flow Chart

Looking for a progressive flow chart centered and branching off. They all build on each other 1-3. There will be 3 different pages.

Target Market(s)

Business Owners - High Net worth Individuals

Industry/Entity Type

Finance & Business Consulting

Font styles to use
Serif

Colors
0054AA
0677BA
7BADD7
CADEEF
E8F1F8
0094D4
00A9DD
6FCCEA
C7EBF8
E9F6FB
00AB8E
00BBA5
67D7C9
C6EFE9
E9F9F6

Requirements
Nice to have
• Clean, simple, and approachable.
Should not have
• Very Busy

```html
<!DOCTYPE html>
<html lang="en">
<head>
<meta charset="utf-8">
<title>Meridel Wealth Partners – Trust Flow Chart</title>
<link rel="stylesheet" href="https://fonts.googleapis.com/css2?family=Lexend:wght@400;500;600;700&display=swap">
<style>
  :root {
    --backdrop: #d6d6d6;
    --navy: #0d1445;
    --navy-deep: #0a1038;
    --glow: #1d3f86;
    --teal-top: #06f2b2;
    --teal-bottom: #0aa7c9;
    --teal-arrow: #19d3b8;
    --ink: #0b1238;
    --white: #ffffff;
    --silver: #c9ccd3;
  }
  * { box-sizing: border-box; margin: 0; padding: 0; }
  html, body { width: 1200px; height: 1011px; overflow: hidden; }
  body { background: var(--backdrop); font-family: "Lexend", sans-serif; position: relative; }

  .sheet {
    position: absolute; left: 72px; top: 94px; width: 1058px; height: 817px;
    background:
      radial-gradient(ellipse 420px 300px at 900px 120px, var(--glow), transparent 70%),
      radial-gradient(ellipse 380px 260px at 100px 760px, #17306c, transparent 70%),
      linear-gradient(160deg, var(--navy) 0%, var(--navy-deep) 100%);
    overflow: hidden;
  }

  .brand {
    position: absolute; left: 44px; top: 62px; width: 260px;
    display: flex; flex-direction: column; align-items: center;
    color: var(--silver); font-weight: 500;
  }
  .brand-mark {
    display: block; width: 110px; height: 110px; border-radius: 50%;
    border: 10px solid var(--silver); margin-bottom: 48px;
  }
  .brand-name { font-size: 40px; letter-spacing: 2px; line-height: 40px; }
  .brand-tag { font-size: 13px; letter-spacing: 4.5px; margin-top: 10px; white-space: nowrap; }

  .tier { position: absolute; top: 137px; height: 80px; }
  .tier-num {
    position: absolute; left: 0; top: 0; width: 46px; height: 80px;
    background: var(--white); border-radius: 6px;
    color: #000; font-weight: 700; font-size: 46px; line-height: 80px; text-align: center; z-index: 1;
  }
  .tier-bar {
    position: absolute; left: 46px; top: 11px; height: 58px;
    background: linear-gradient(180deg, var(--teal-top), var(--teal-bottom));
    border-radius: 0 4px 14px 0;
    color: var(--ink); font-weight: 500; font-size: 19px; line-height: 58px; padding-left: 15px;
  }

  .pill {
    position: absolute; width: 267px; height: 90px; border-radius: 32px;
    background: linear-gradient(180deg, var(--teal-top), var(--teal-bottom));
    color: var(--ink);
  }
  .pill-icon {
    position: absolute; left: 8px; top: 13px; width: 64px; height: 64px; border-radius: 50%;
    background: linear-gradient(180deg, var(--teal-top), var(--teal-bottom));
    border: 5px solid #e9f1f4; box-shadow: 0 2px 6px rgba(0,0,0,.25);
    display: flex; align-items: center; justify-content: center;
  }
  .pill-icon svg { width: 28px; height: 28px; fill: var(--ink); }
  .pill-title { position: absolute; left: 86px; top: 14px; font-weight: 500; font-size: 24px; line-height: 23px; letter-spacing: .3px; }
  .pill-note { position: absolute; left: 86px; font-size: 12.5px; line-height: 16px; font-weight: 500; }

  .step {
    position: absolute; width: 22px; height: 22px; border-radius: 50%;
    background: var(--navy); border: 2px solid var(--white);
    color: var(--white); font-size: 11px; font-weight: 600; line-height: 18px; text-align: center;
  }
  .pill .step { right: 20px; top: 15px; }

  .trust {
    position: absolute; left: 416px; top: 274px; width: 216px; height: 216px; border-radius: 50%;
    background: linear-gradient(180deg, var(--teal-top), var(--teal-bottom));
    border: 3px solid #c7ccd2;
  }
  .trust-label { position: absolute; top: 25px; width: 100%; text-align: center; font-size: 11.5px; font-weight: 600; color: var(--ink); }
  .trust-core {
    position: absolute; left: 43px; top: 43px; width: 124px; height: 124px; border-radius: 50%;
    background: var(--white); border: 4px solid #9aa1ac;
    display: flex; flex-direction: column; align-items: center; justify-content: center;
    color: var(--ink); font-weight: 600; font-size: 15px; line-height: 16px; text-align: center;
  }
  .trust-dot { width: 26px; height: 26px; border-radius: 50%; background: var(--teal-bottom); margin-bottom: 10px; }
  .trust .step { left: 95px; top: -13px; }

  .flow { position: absolute; left: 0; top: 0; width: 1058px; height: 817px; }
  .flow line { stroke: var(--white); stroke-width: 2; stroke-dasharray: 0.1 4; stroke-linecap: round; fill: none; }
  .flow-label { fill: var(--white); font-family: "Lexend", sans-serif; font-size: 10px; letter-spacing: .5px; }
</style>
</head>
<body>
<main class="sheet">

  <div class="brand">
    <span class="brand-mark"></span>
    <div class="brand-name">MERIDEL</div>
    <div class="brand-tag">WEALTH PARTNERS</div>
  </div>

  <div class="tier" style="left:300px;width:290px"><div class="tier-num">3</div><div class="tier-bar" style="width:170px">CRT</div></div>
  <div class="tier" style="left:544px;width:290px"><div class="tier-num">3</div><div class="tier-bar" style="width:167px">DAF</div></div>
  <div class="tier" style="left:789px;width:290px"><div class="tier-num">3</div><div class="tier-bar" style="width:166px">GRATS' IDGT'S</div></div>

  <svg class="flow" viewBox="0 0 1058 817" aria-hidden="true">
    <defs>
      <marker id="arrow" viewBox="0 0 10 10" refX="8" refY="5" markerWidth="7" markerHeight="7" orient="auto">
        <path d="M0 0 L10 5 L0 10 L3 5 Z" fill="#19d3b8"/>
      </marker>
    </defs>
    <line x1="518" y1="177" x2="544" y2="177"/>
    <line x1="763" y1="177" x2="789" y2="177"/>
    <line x1="416" y1="382" x2="326" y2="382" marker-end="url(#arrow)"/>
    <line x1="165" y1="636" x2="165" y2="432" marker-end="url(#arrow)"/>
    <line x1="189" y1="430" x2="189" y2="634" marker-end="url(#arrow)"/>
    <line x1="186" y1="428" x2="498" y2="632" marker-end="url(#arrow)"/>
    <line x1="192" y1="636" x2="430" y2="476" marker-end="url(#arrow)"/>
    <line x1="524" y1="636" x2="524" y2="494" marker-end="url(#arrow)"/>
    <line x1="594" y1="468" x2="690" y2="534" marker-end="url(#arrow)"/>
    <line x1="690" y1="534" x2="836" y2="636"/>
    <line x1="884" y1="636" x2="712" y2="508" marker-end="url(#arrow)"/>
    <line x1="712" y1="508" x2="614" y2="448"/>
    <text class="flow-label" x="358" y="398">INVEST</text>
    <text class="flow-label" transform="translate(150 550) rotate(-90)">INTEREST</text>
    <text class="flow-label" transform="translate(204 558) rotate(-90)">INVESTMENT</text>
    <text class="flow-label" transform="translate(542 576) rotate(-90)">INCOME</text>
  </svg>

  <div class="trust">
    <span class="step">1</span>
    <div class="trust-label">LIVING TRUST</div>
    <div class="trust-core"><span class="trust-dot"></span>YOU<br>TRUSTEE</div>
  </div>

  <section class="pill" style="left:54px;top:338px">
    <div class="pill-icon"><svg viewBox="0 0 24 24"><path d="M12 2 2 7v2h20V7zM4 10h3v8H4zm6.5 0h3v8h-3zM17 10h3v8h-3zM2 19h20v3H2z"/></svg></div>
    <div class="pill-title">BANK</div>
    <div class="pill-note" style="top:46px">Makes investments to real<br>estate + business</div>
    <span class="step">2</span>
  </section>

  <section class="pill" style="left:54px;top:638px">
    <div class="pill-icon"><svg viewBox="0 0 24 24"><path d="M7 3h10v18H7zm2 2v2h2V5zm4 0v2h2V5zM9 9v2h2V9zm4 0v2h2V9zm-4 4v2h2v-2zm4 0v2h2v-2zm-2 4v4h2v-4zM2 10h4v11H2zm16 0h4v11h-4z"/></svg></div>
    <div class="pill-title">REAL<br>ESTATE</div>
    <div class="pill-note" style="top:64px">LLC</div>
    <span class="step">1</span>
  </section>

  <section class="pill" style="left:396px;top:638px">
    <div class="pill-icon"><svg viewBox="0 0 24 24"><path d="M9 3h6a1 1 0 0 1 1 1v2h5a1 1 0 0 1 1 1v4H2V7a1 1 0 0 1 1-1h5V4a1 1 0 0 1 1-1zm1 2v1h4V5zM2 13h8v2h4v-2h8v7a1 1 0 0 1-1 1H3a1 1 0 0 1-1-1z"/></svg></div>
    <div class="pill-title">BUSINESS</div>
    <div class="pill-note" style="top:46px">LLC-member/manager<br>corp= president</div>
    <span class="step">1</span>
  </section>

  <section class="pill" style="left:738px;top:638px">
    <div class="pill-icon"><svg viewBox="0 0 24 24"><path d="M4 2h10l4 4v5h-2V7h-3V4H6v16h6v2H4zm3 6h6v2H7zm0 4h5v2H7zm11 0 5 2v3c0 3-2 5-5 6-3-1-5-3-5-6v-3z"/></svg></div>
    <div class="pill-title" style="top:33px">INSURANCE</div>
    <span class="step">2</span>
  </section>

</main>
</body>
</html>
```